Business Card for Coastal Tundrabridge Advisory

We need a business card for Coastal Tundrabridge Advisory. The company website address is provided below. The company logo is attached. We provide specialized permafrost services to the mining, transportation, and oil & gas industries. The card should be prepared for:
Matthias Korhonen, PhD.
Coastal Tundrabridge Advisory
PO Box 418259
Quillwater, Alaska 99642
Direct: +1-907-555-0143
Email: mkorhonen@tundrabridgeadvisory.example
Website: www.coastaltundrabridgeadvisory.example

```html
<!DOCTYPE html>
<html lang="en">
<head>
<meta charset="utf-8">
<title>Coastal Tundrabridge Advisory — Business Card</title>
<link href="https://fonts.googleapis.com/css2?family=Montserrat:wght@300;600;700&family=Roboto:wght@400;500&family=Open+Sans:wght@400&display=swap" rel="stylesheet">
<style>
  :root {
    --backdrop: #232323;
    --card: #121723;
    --card-edge: #1b2232;
    --ink: #ffffff;
    --ink-soft: #e6e8ee;
    --emboss: #26336a;
  }
  * { box-sizing: border-box; margin: 0; padding: 0; }
  html, body { width: 1200px; height: 711px; overflow: hidden; background: var(--backdrop); }
  .stage {
    position: relative; width: 1200px; height: 711px;
    display: flex; align-items: center; justify-content: center; gap: 48px;
  }
  .card {
    position: relative; width: 520px; height: 297px;
    background: var(--card); border-radius: 22px;
    box-shadow: 0 10px 30px rgba(0,0,0,.45);
    overflow: hidden;
  }
  .wordmark {
    font-family: "Montserrat", sans-serif; font-weight: 600;
    text-transform: uppercase; line-height: 1.05;
  }
  .card-front .wordmark {
    position: absolute; left: 0; right: 0; top: 92px;
    text-align: center; font-size: 27px; letter-spacing: 3px; color: var(--emboss);
  }
  .services {
    position: absolute; left: 20px; right: 20px; bottom: 34px;
    text-align: center; font-family: "Roboto", sans-serif; color: var(--ink-soft);
  }
  .services-title { font-size: 10px; font-weight: 500; letter-spacing: .3px; margin-bottom: 3px; }
  .services-text { font-size: 9.6px; font-weight: 400; }

  .card-back .wordmark {
    position: absolute; right: 30px; top: 34px; width: 250px;
    text-align: right; font-size: 20px; letter-spacing: 2px; color: var(--ink);
  }
  .holder {
    position: absolute; left: 30px; bottom: 24px;
    transform-origin: left bottom; transform: rotate(-90deg) translate(0, 100%);
    font-family: "Montserrat", sans-serif; color: var(--ink); white-space: nowrap;
  }
  .holder-name { font-size: 26px; line-height: 1.1; }
  .holder-name .first { font-weight: 700; }
  .holder-name .last { font-weight: 300; }
  .holder-degree { font-size: 13px; font-weight: 300; }

  .contact {
    position: absolute; right: 26px; bottom: 30px;
    font-family: "Open Sans", sans-serif; color: var(--ink); font-size: 11px;
    text-align: right; line-height: 1.45;
  }
  .address { margin-bottom: 10px; }
  .contact-line { display: flex; justify-content: flex-end; align-items: center; gap: 8px; }
  .contact-line svg { width: 11px; height: 11px; flex: none; }
  .address .contact-line { padding-right: 19px; }
</style>
</head>
<body>
<main class="stage">
  <section class="card card-front" aria-label="Business card front">
    <p class="wordmark">Coastal Tundrabridge<br>Advisory</p>
    <div class="services">
      <p class="services-title">OUR SERVICES</p>
      <p class="services-text">We provide specialized permafrost services to the mining, transportation, and oil &amp; gas industries</p>
    </div>
  </section>

  <section class="card card-back" aria-label="Business card back">
    <p class="wordmark">Coastal Tundrabridge<br>Advisory</p>
    <div class="holder">
      <p class="holder-name"><span class="first">Matthias</span> <span class="last">Korhonen</span></p>
      <p class="holder-degree">PhD</p>
    </div>
    <div class="contact">
      <div class="address">
        <p class="contact-line">PO Box 418259</p>
        <p class="contact-line">Quillwater, Alaska 99642</p>
      </div>
      <p class="contact-line">+1-907-555-0143
        <svg viewBox="0 0 12 12" aria-hidden="true"><path d="M3 1l2 2.2-1.1 1.3a6 6 0 0 0 3.6 3.6L8.8 7 11 9l-1.4 1.8C5 10.6 1.4 7 1.2 2.4z" fill="#fff"/></svg>
      </p>
      <p class="contact-line">mkorhonen@tundrabridgeadvisory.example
        <svg viewBox="0 0 12 12" aria-hidden="true"><rect x="1" y="2.5" width="10" height="7" fill="none" stroke="#fff" stroke-width="1.2"/><path d="M1 2.8l5 4 5-4" fill="none" stroke="#fff" stroke-width="1.2"/></svg>
      </p>
      <p class="contact-line">www.coastaltundrabridgeadvisory.example
        <svg viewBox="0 0 12 12" aria-hidden="true"><circle cx="6" cy="6" r="5" fill="none" stroke="#fff" stroke-width="1.1"/><ellipse cx="6" cy="6" rx="2.2" ry="5" fill="none" stroke="#fff" stroke-width="1"/><path d="M1 6h10" stroke="#fff" stroke-width="1"/></svg>
      </p>
    </div>
  </section>
</main>
</body>
</html>
```